Dynamic Business Card for Sports Supplements Company

Hi! I'm looking for an awesome business card to match my existing sports supplement company. I have uploaded my current company logo and screenshot of the front page of my website.

I would like to have something dynamic and interesting and utilize the colors in the website - the reds and purples

The business card should be double sided and focus on a unique eye-catching design on the back and include all the relevant company info.

Most importantly, it should say somewhere: "Sign up on our website for a coupon code."

Target Market(s)

Mostly for women gym goers but it shouldn't be too feminine. It should be in keeping with the website design. It should flow and clearly be connected to it

Industry/Entity Type

Business

Contact Information for Business Card

Lorraine K. Vestal
CEO
LVestal@Quorvanexco.com
www.quorvanexco.com
555.417.3820
P.O. Box 47315
Larkfield, Oregon 00000

Sign up on our website for a coupon code

Font styles to use
Serif
Sans Serif
Other font styles liked:
• Novecento font family and "Quorvanex" is in AR Destine font

Requirements
Must have
• One side should be a bold Quorvanex logo design. Even just the symbol itself may be o.k. (see attached file)

```html
<!DOCTYPE html>
<html lang="en">
<head>
<meta charset="utf-8">
<title>Quorvanex Business Card</title>
<link rel="stylesheet" href="https://fonts.googleapis.com/css2?family=Source+Sans+3:ital,wght@0,400;0,600;0,700;1,400&display=swap">
<style>
  :root {
    --stage: #d8d3cd;
    --card-black: #000000;
    --brand-red: #e31e24;
    --paper-white: #ffffff;
    --text-white: #f4f4f4;
    --tagline-grey: #9a9a9a;
    --url-dark: #222222;
    --pattern-dark: #1c1617;
    --pattern-mid: #2a2022;
  }
  * { box-sizing: border-box; margin: 0; padding: 0; }
  html, body {
    width: 1200px;
    height: 987px;
    overflow: hidden;
  }
  body {
    position: relative;
    background: var(--stage);
    font-family: "Source Sans 3", Arial, sans-serif;
    color: var(--text-white);
  }
  .card {
    position: absolute;
    left: 293px;
    width: 615px;
    height: 352px;
    background: var(--card-black);
    box-shadow: 0 4px 14px rgba(0,0,0,0.35);
    overflow: hidden;
  }
  .card--front { top: 130px; }
  .card--back { top: 506px; }

  /* Front */
  .brand-mark {
    position: absolute;
    left: 106px;
    top: 36px;
    width: 70px;
    height: 70px;
    background: var(--brand-red);
  }
  .brand-name {
    position: absolute;
    left: 41px;
    top: 116px;
    font-size: 35px;
    font-weight: 700;
    letter-spacing: 0.8px;
    color: var(--paper-white);
    text-transform: uppercase;
    line-height: 1;
  }
  .brand-tagline {
    position: absolute;
    left: 42px;
    top: 150px;
    font-size: 9.5px;
    letter-spacing: 3.1px;
    color: var(--tagline-grey);
    text-transform: uppercase;
    white-space: nowrap;
  }
  .contact {
    position: absolute;
    left: 41px;
    top: 196px;
    font-size: 15.5px;
    line-height: 23px;
  }
  .contact__phone { margin-top: 6px; }
  .contact__label { color: var(--brand-red); font-weight: 600; }
  .person {
    position: absolute;
    right: 36px;
    top: 226px;
    text-align: right;
  }
  .person__name {
    font-size: 20px;
    font-weight: 600;
    color: var(--brand-red);
    letter-spacing: 0.5px;
    text-transform: uppercase;
  }
  .person__role {
    font-size: 16px;
    margin-top: 2px;
  }
  .web-band {
    position: absolute;
    left: 0;
    bottom: 0;
    width: 615px;
    height: 30px;
    background: var(--paper-white);
  }
  .web-band__url {
    position: absolute;
    left: 0;
    width: 610px;
    top: 4px;
    text-align: center;
    font-size: 15.5px;
    font-weight: 600;
    color: var(--url-dark);
  }
  .web-band__url span { color: var(--brand-red); }
  .web-band__arrows {
    position: absolute;
    right: 0;
    top: 0;
  }

  /* Back */
  .back-pattern {
    position: absolute;
    inset: 0;
    background: linear-gradient(160deg, var(--pattern-mid), var(--pattern-dark) 55%, #120e0f);
  }
  .back-mark {
    position: absolute;
    left: 0;
    width: 615px;
    top: 160px;
    text-align: center;
    font-size: 30px;
    font-weight: 700;
    color: var(--paper-white);
    text-transform: uppercase;
    line-height: 1;
  }
  .back-mark__square {
    display: inline-block;
    width: 24px;
    height: 24px;
    background: var(--brand-red);
    margin-right: 10px;
    vertical-align: -2px;
  }
  .back-offer {
    position: absolute;
    left: 0;
    width: 615px;
    top: 278px;
    text-align: center;
    font-size: 16.5px;
    font-style: italic;
    color: var(--text-white);
  }
</style>
</head>
<body>
  <section class="card card--front" aria-label="Business card front">
    <div class="brand-mark"></div>
    <div class="brand-name">Quorvanex</div>
    <div class="brand-tagline">Your Strength Companion</div>

    <div class="contact">
      <p>P.O. Box 47315</p>
      <p>Larkfield, Oregon 00000</p>
      <p class="contact__phone"><span class="contact__label">Phone:</span> 555.417.3820</p>
      <p>LVestal@Quorvanexco.com</p>
    </div>

    <div class="person">
      <p class="person__name">Lorraine K. Vestal</p>
      <p class="person__role">CEO</p>
    </div>

    <div class="web-band">
      <p class="web-band__url"><span>www.</span>quorvanexco<span>.com</span></p>
      <svg class="web-band__arrows" width="102" height="30" viewBox="0 0 102 30" aria-hidden="true">
        <polygon points="12,15 24,2 28,2 16,15 28,28 24,28" fill="#000"/>
        <polygon points="22,15 34,2 38,2 26,15 38,28 34,28" fill="#000"/>
        <polygon points="32,15 45,0 102,0 102,30 45,30" fill="#e31e24"/>
      </svg>
    </div>
  </section>

  <section class="card card--back" aria-label="Business card back">
    <div class="back-pattern" role="img" aria-label="Repeating dark chevron pattern in black, charcoal and deep red"></div>
    <div class="back-mark"><span class="back-mark__square"></span>Quorvanex</div>
    <p class="back-offer">Sign up on our website for a coupon code</p>
  </section>
</body>
</html>
```